one pager for investors

I will give an initial file in any format needed. Also, the photo that must be included. As well as the logo, that must be the key to the overall design in terms of font, colors, and general layout. I will attach a file in PDF format, which is a one pager presenting a project for investors that I would like to attract and convinced to invest in my project. What I would like you to do is propose me different and better design options, taking my first draft as an example. But you must absolutely keep every single word and number, absolutely all the information written in my first draft(except “ TEMPLATE DRAFT”). Also, on the top left corner is the logo of our company, which I think should be your main inspiration document is a one pager presented to potential investors that not only has to include the most important information in order for them to be able to see everything needed to see the value of the project (which I’ve already taken care of by writing the text needed, numbers presented and timeline shown; all of which which must be preserved in terms of content, but can be completely redesigned and manipulated ) sh a.k.a. Project summary for investor to go for it.
Serious rich investors
Real eatate

```html
<!DOCTYPE html>
<html lang="fr">
<head>
<meta charset="utf-8">
<title>Projet immobilier – One pager investisseurs</title>
<link href="https://fonts.googleapis.com/css2?family=Poppins:wght@500;600;700&family=Questrial&display=swap" rel="stylesheet">
<style>
  :root{
    --blue:#2e50b4;
    --blue-light:#dde4fb;
    --band:#cfdaf8;
    --ink:#1f1f1f;
    --dark:#222222;
    --grey:#a9abb2;
    --white:#ffffff;
    --backdrop:#e9ecf2;
  }
  *{margin:0;padding:0;box-sizing:border-box}
  html,body{width:1200px;height:1200px;overflow:hidden;background:var(--backdrop)}
  body{position:relative;font-family:"Questrial",sans-serif;color:var(--ink)}
  .page{
    position:absolute;left:152px;top:20px;width:1245px;height:1612px;
    background:var(--white);transform:scale(.72);transform-origin:0 0;
  }
  .abs{position:absolute}

  .conf-title{left:97px;top:72px;font-family:"Poppins",sans-serif;font-weight:700;font-size:35px;letter-spacing:5px;color:var(--blue)}
  .project-name{left:100px;top:120px;font-size:29px;color:var(--ink)}

  .brand{right:94px;top:106px;display:flex;align-items:center;gap:16px}
  .brand-mark{width:28px;height:28px;background:var(--blue)}
  .brand-name{font-family:"Poppins",sans-serif;font-weight:600;font-size:32px;color:var(--ink);line-height:1}

  .accent-bar{left:66px;top:199px;width:569px;height:20px;background:var(--blue)}
  .hero{left:66px;top:219px;width:1106px;height:450px;
    background:linear-gradient(180deg,#c9cfd6 0%,#d8d6cf 35%,#9a8370 55%,#5f6b45 80%,#3f4a2c 100%)}

  .desc{left:66px;top:669px;width:569px;height:314px;background:var(--blue);color:var(--white);padding:26px 30px 0 54px}
  .desc h2{font-family:"Poppins",sans-serif;font-weight:600;font-size:33px;margin-bottom:16px}
  .desc p{font-size:21px;line-height:28.6px;letter-spacing:.7px}
  .duration{left:66px;top:983px;width:569px;height:75px;background:var(--dark);color:var(--white);
    font-family:"Poppins",sans-serif;font-weight:600;font-size:23px;padding:20px 0 0 54px}

  .section-title{font-family:"Poppins",sans-serif;font-weight:600;font-size:35px;color:var(--ink)}

  .row{position:absolute;height:31px;display:flex;align-items:center;font-size:20px;color:#333}
  .row .label{padding-left:13px}
  .row .val{position:absolute}
  .row.tint{background:var(--blue-light)}
  .row.blue{background:var(--blue);color:var(--white);font-family:"Poppins",sans-serif;font-weight:600}
  .row.black{background:var(--dark);color:var(--white);font-family:"Poppins",sans-serif;font-weight:600}
  .row.tint.strong{font-family:"Poppins",sans-serif;font-weight:600;color:var(--ink)}
  .row .val.plain{font-family:"Questrial",sans-serif;font-weight:400}

  .fin .row{left:693px;width:456px}
  .fin .val{left:300px}
  .inv .row{left:66px;width:456px}
  .inv .val{left:303px}
  .inv .val.wide{left:348px}
  .note{font-size:17px;color:#333}
  .calc{font-family:"Poppins",sans-serif;font-weight:500;font-style:italic;font-size:17px;color:var(--blue)}

  .timeline{left:580px;top:1100px;width:600px;height:280px}
  .timeline text{font-family:"Poppins",sans-serif}

  .rule{left:68px;top:1423px;width:1108px;height:2px;background:var(--grey)}
  .tab{left:934px;top:1424px;width:244px;height:28px;background:var(--grey);
    clip-path:polygon(0 0,100% 0,100% 100%,18px 100%);color:var(--white);font-size:15px;
    letter-spacing:9px;padding:5px 0 0 34px;font-family:"Poppins",sans-serif;font-weight:500}

  .foot-mark{left:86px;top:1468px;width:62px;height:62px;background:var(--blue)}
  .company{left:192px;top:1456px;font-family:"Poppins",sans-serif;font-weight:600;font-size:21px;color:var(--ink)}
  .company span{color:var(--blue)}
  .address{left:192px;top:1486px;font-size:26px;line-height:30px;color:var(--ink)}
  .contact{top:1496px;display:flex;align-items:center;gap:17px;font-family:"Poppins",sans-serif;font-weight:500;font-size:18px;color:var(--ink)}
  .contact svg{width:36px;height:36px;display:block}
</style>
</head>
<body>
<div class="page">
  <div class="abs conf-title">CONFIDENTIEL</div>
  <div class="abs project-name">Projet imobilier “XXX”</div>

  <div class="abs brand">
    <div class="brand-mark"></div>
    <div class="brand-name">HALVREN PROPERTIES SA</div>
  </div>

  <div class="abs accent-bar"></div>
  <div class="abs hero" role="img" aria-label="Visualisation de l’immeuble résidentiel avec terrasses, entouré d’arbres et de jardins"></div>

  <div class="abs desc">
    <h2>Description du projet</h2>
    <p>Le projet XXX est un projet de dévloppement de 30 appartements de standing en PPE au centre de Lausanne. Le terrain a été sécurisé par la signature du vente à terme conditionnelle. L’objectif est d’obtenir le permis de construire, puis de ventre les lots. Dans un premier temps sur plan puis au fil de la construction.</p>
  </div>
  <div class="abs duration">Durée estimée du projet – 24 à 36 mois.</div>

  <div class="abs section-title" style="left:704px;top:686px">Plan financier</div>
  <div class="fin">
    <div class="row tint" style="top:749px"><span class="label">Prix du terrain</span><span class="val">CHF 2’000’000</span></div>
    <div class="row" style="top:780px"><span class="label">Frais d’acquisition</span><span class="val">CHF 100’000</span></div>
    <div class="row tint" style="top:811px"><span class="label">Coût de construction</span><span class="val">CHF 2’500’000</span></div>
    <div class="row" style="top:842px"><span class="label">Divers &amp; imprévus</span><span class="val">CHF 200’000</span></div>
    <div class="row blue" style="top:879px"><span class="label">Prix de revient total</span><span class="val">CHF 4’800’000</span></div>
    <div class="row black" style="top:925px"><span class="label">Prix de vente total</span><span class="val">CHF 7’500’000</span></div>
    <div class="row tint" style="top:956px"><span class="label">Honoraires sur vente</span><span class="val">CHF 190’000</span></div>
    <div class="row blue" style="top:1002px"><span class="label">Marge projet</span><span class="val">CHF 2’510’000</span></div>
    <div class="row tint strong" style="top:1033px"><span class="label">En % sur prix de vente</span><span class="val">33.47%</span></div>
  </div>

  <div class="abs section-title" style="left:66px;top:1092px">Structure d’investissement</div>
  <div class="inv">
    <div class="row tint" style="top:1157px"><span class="label">Besoin de fonds propres</span><span class="val">CHF 2’000’000</span></div>
    <div class="row" style="top:1188px"><span class="label">Retour de fonds total</span><span class="val">CHF 3’156’600</span></div>
    <div class="row black" style="top:1223px"><span class="label">Bénéfice net investisseur</span><span class="val">CHF 1’656’600</span></div>
    <div class="abs note" style="left:81px;top:1257px">Soit 2/3 du bénéfice projet</div>
    <div class="row blue" style="top:1290px"><span class="label">Multiple sur fonds propres</span><span class="val wide plain">x1.83</span></div>
    <div class="row black" style="top:1329px"><span class="label">Rendement annualisé</span><span class="val wide plain">41.4%</span></div>
    <div class="abs calc" style="left:81px;top:1363px">Calcul sur 24 mois</div>
  </div>

  <svg class="abs timeline" viewBox="580 1100 600 280" aria-label="Calendrier du projet">
    <rect x="643" y="1237" width="468" height="18" fill="var(--band)"/>
    <g fill="none" stroke="#ffffff" stroke-width="3">
      <polyline points="712,1239 719,1246 712,1253"/><polyline points="722,1239 729,1246 722,1253"/>
      <polyline points="866,1239 873,1246 866,1253"/><polyline points="876,1239 883,1246 876,1253"/>
      <polyline points="1024,1239 1031,1246 1024,1253"/><polyline points="1034,1239 1041,1246 1034,1253"/>
    </g>
    <g stroke="var(--blue)" stroke-width="3">
      <line x1="643" y1="1164" x2="643" y2="1206"/><line x1="643" y1="1286" x2="643" y2="1325"/>
      <line x1="798" y1="1156" x2="798" y2="1206"/><line x1="798" y1="1286" x2="798" y2="1314"/>
      <line x1="949" y1="1164" x2="949" y2="1206"/><line x1="949" y1="1286" x2="949" y2="1323"/>
      <line x1="1111" y1="1156" x2="1111" y2="1206"/><line x1="1111" y1="1286" x2="1111" y2="1312"/>
    </g>
    <g fill="var(--blue)"><circle cx="643" cy="1164" r="3.5"/><circle cx="798" cy="1314" r="3.5"/><circle cx="949" cy="1164" r="3.5"/></g>
    <g>
      <circle cx="643" cy="1246" r="37" fill="#fff" stroke="var(--blue)" stroke-width="7"/>
      <circle cx="798" cy="1246" r="37" fill="#fff" stroke="var(--blue)" stroke-width="7"/>
      <circle cx="949" cy="1246" r="37" fill="#fff" stroke="var(--blue)" stroke-width="7"/>
      <circle cx="1111" cy="1246" r="37" fill="#fff" stroke="var(--blue)" stroke-width="7"/>
      <g fill="var(--band)"><circle cx="643" cy="1246" r="26"/><circle cx="798" cy="1246" r="26"/><circle cx="949" cy="1246" r="26"/><circle cx="1111" cy="1246" r="26"/></g>
    </g>
    <g fill="none" stroke="var(--blue)" stroke-width="2" stroke-linejoin="round" stroke-linecap="round">
      <polyline points="629,1248 643,1234 657,1248"/><rect x="633" y="1244" width="20" height="13"/><line x1="627" y1="1260" x2="659" y2="1260"/>
      <circle cx="798" cy="1244" r="15"/><path d="M793,1240 a5,5 0 1 1 6,5 v3"/><line x1="799" y1="1252" x2="799" y2="1253"/>
      <rect x="935" y="1246" width="28" height="14"/><line x1="935" y1="1253" x2="963" y2="1253"/><line x1="945" y1="1246" x2="945" y2="1253"/><line x1="954" y1="1253" x2="954" y2="1260"/><line x1="950" y1="1246" x2="962" y2="1232"/>
      <circle cx="1104" cy="1240" r="7"/><line x1="1109" y1="1245" x2="1122" y2="1258"/><line x1="1117" y1="1253" x2="1113" y2="1257"/><line x1="1121" y1="1257" x2="1117" y2="1261"/>
    </g>
    <g fill="var(--blue)">
      <rect x="599" y="1323" width="88" height="24" rx="12"/>
      <rect x="754" y="1132" width="88" height="24" rx="12"/>
      <rect x="905" y="1323" width="88" height="24" rx="12"/>
      <rect x="1067" y="1132" width="88" height="24" rx="12"/>
    </g>
    <g fill="#fff" font-size="17" font-weight="500" text-anchor="middle">
      <text x="643" y="1341">08.2024</text><text x="798" y="1150">04.2025</text>
      <text x="949" y="1341">12.2025</text><text x="1111" y="1150">12.2025</text>
    </g>
    <g fill="var(--ink)" font-size="19" font-weight="500" text-anchor="middle">
      <text x="643" y="1125">Achat</text><text x="643" y="1150">parcelle</text>
      <text x="949" y="1125">Début</text><text x="949" y="1150">construction</text>
      <text x="798" y="1335">Mise à</text><text x="798" y="1360">l’enquête</text>
      <text x="1111" y="1344">Livraison</text>
    </g>
  </svg>

  <div class="abs rule"></div>
  <div class="abs tab">CONFIDENTIEL</div>

  <div class="abs foot-mark"></div>
  <div class="abs company">HALVREN PROPERTIES <span>VAUD SA</span></div>
  <div class="abs address">Chemin des Aulnes 7<br>CH-1185 Valmont</div>

  <div class="abs contact" style="left:553px">
    <svg viewBox="0 0 36 36"><circle cx="18" cy="18" r="18" fill="var(--blue)"/><path d="M11 14 q7-5 14 0 l-2 3 h-3 v-2 h-4 v2 h-3 z M12 19 h12 v6 h-12 z" fill="#fff"/></svg>
    <span>079 000 12 34</span>
  </div>
  <div class="abs contact" style="left:771px">
    <svg viewBox="0 0 36 36"><circle cx="18" cy="18" r="18" fill="var(--blue)"/><rect x="10" y="12" width="16" height="12" fill="#fff"/><polyline points="10,12 18,19 26,12" fill="none" stroke="var(--blue)" stroke-width="1.5"/></svg>
    <span>info@halvren.ch</span>
  </div>
  <div class="abs contact" style="left:991px">
    <svg viewBox="0 0 36 36"><circle cx="18" cy="18" r="18" fill="var(--blue)"/><g fill="none" stroke="#fff" stroke-width="1.5"><circle cx="18" cy="18" r="9"/><ellipse cx="18" cy="18" rx="4" ry="9"/><line x1="9" y1="18" x2="27" y2="18"/><line x1="10.5" y1="13.5" x2="25.5" y2="13.5"/><line x1="10.5" y1="22.5" x2="25.5" y2="22.5"/></g></svg>
    <span>www.halvren.ch</span>
  </div>
</div>
</body>
</html>
```